Copper Lantern

Need a business card for our restaurant. Restaurant and Bar in the mountains of North Idaho. Rustic looking card

rustic design, wood and metal looking, primarily neutral colors

• Name, address, phone number, website, email address

```html
<!DOCTYPE html>
<html lang="en">
<head>
<meta charset="utf-8">
<title>Copper Lantern – Business Card</title>
<link href="https://fonts.googleapis.com/css2?family=Lexend:wght@400;600;700&display=swap" rel="stylesheet">
<style>
  :root {
    --backdrop: #d1d5d7;
    --ink: #111111;
    --paper: #ffffff;
    --sand-light: #e6d3a8;
    --sand-mid: #cdb48e;
    --clay: #a98c7a;
    --clay-deep: #96796a;
  }
  html, body {
    margin: 0;
    width: 900px;
    height: 1200px;
    overflow: hidden;
    background: var(--backdrop);
    font-family: "Lexend", sans-serif;
    color: var(--ink);
  }
  .card {
    position: absolute;
    left: 136px;
    width: 631px;
    border-radius: 14px;
    overflow: hidden;
  }
  .card--front { top: 216px; height: 356px; }
  .card--back { top: 629px; height: 359px; background: var(--paper); }

  .front-texture {
    position: absolute;
    inset: 0;
    background:
      radial-gradient(ellipse 40% 35% at 50% 45%, var(--sand-light) 0%, transparent 70%),
      radial-gradient(ellipse 30% 30% at 80% 40%, var(--sand-light) 0%, transparent 70%),
      radial-gradient(ellipse 35% 30% at 12% 60%, var(--sand-light) 0%, transparent 70%),
      radial-gradient(ellipse 45% 25% at 20% 8%, var(--clay) 0%, transparent 70%),
      radial-gradient(ellipse 40% 30% at 85% 92%, var(--clay-deep) 0%, transparent 70%),
      radial-gradient(ellipse 40% 25% at 35% 95%, var(--clay) 0%, transparent 70%),
      var(--sand-mid);
  }

  .brand-seal {
    position: absolute;
    border: 4px solid var(--ink);
    border-radius: 50%;
    display: flex;
    align-items: center;
    justify-content: center;
    box-sizing: border-box;
  }
  .brand-name {
    font-weight: 600;
    text-transform: uppercase;
    letter-spacing: 0.12em;
    text-align: center;
    line-height: 1.25;
    color: var(--ink);
  }
  .card--front .brand-seal { left: 181px; top: 45px; width: 266px; height: 266px; }
  .card--front .brand-name { font-size: 26px; }
  .card--back .brand-seal { left: 63px; top: 72px; width: 214px; height: 214px; }
  .card--back .brand-name { font-size: 21px; }

  .contact {
    position: absolute;
    left: 301px;
    top: 66px;
  }
  .contact__name {
    margin: 0;
    font-size: 23px;
    font-weight: 700;
    letter-spacing: 0.03em;
    line-height: 1.1;
  }
  .contact__role {
    margin: 2px 0 0;
    font-size: 14px;
    letter-spacing: 0.03em;
  }
  .contact__address {
    margin: 28px 0 0;
    font-size: 14px;
    font-style: normal;
    letter-spacing: 0.06em;
    line-height: 23px;
  }
  .contact__list {
    list-style: none;
    margin: 16px 0 0;
    padding: 0;
    font-size: 14px;
  }
  .contact__list li {
    display: flex;
    align-items: center;
    gap: 7px;
    height: 29px;
    letter-spacing: 0.04em;
  }
  .contact__list .phone-number { letter-spacing: 0.2em; }
  .contact__list svg { width: 16px; height: 16px; flex: none; }

  .services {
    position: absolute;
    left: 0;
    right: 0;
    top: 307px;
    height: 31px;
    background: var(--ink);
    color: var(--paper);
    font-size: 15px;
    font-weight: 600;
    letter-spacing: 0.03em;
    display: flex;
    align-items: center;
    justify-content: space-between;
    padding: 0 48px;
  }
</style>
</head>
<body>

  <section class="card card--front">
    <div class="front-texture" role="img" aria-label="Rustic watercolor wash in sand and clay tones"></div>
    <div class="brand-seal">
      <span class="brand-name">Copper<br>Lantern</span>
    </div>
  </section>

  <section class="card card--back">
    <div class="brand-seal">
      <span class="brand-name">Copper<br>Lantern</span>
    </div>

    <div class="contact">
      <h1 class="contact__name">MARTIN COLE</h1>
      <p class="contact__role">Founder</p>
      <address class="contact__address">214 Ridge Ave,<br>Pine Hollow, ID 83999</address>
      <ul class="contact__list">
        <li>
          <svg viewBox="0 0 24 24" aria-hidden="true"><path fill="#111" d="M6.6 10.8a15.1 15.1 0 0 0 6.6 6.6l2.2-2.2a1 1 0 0 1 1-.25 11.4 11.4 0 0 0 3.6.57 1 1 0 0 1 1 1V20a1 1 0 0 1-1 1A17 17 0 0 1 3 4a1 1 0 0 1 1-1h3.5a1 1 0 0 1 1 1c0 1.25.2 2.45.57 3.57a1 1 0 0 1-.25 1z"/></svg>
          <span class="phone-number">(208) 555-0147</span>
        </li>
        <li>
          <svg viewBox="0 0 24 24" aria-hidden="true"><path fill="#111" d="M2 5h20v14H2z"/><path fill="none" stroke="#fff" stroke-width="1.6" d="M2.5 5.5 12 13l9.5-7.5"/></svg>
          <span>info@thecopperlanternpinehollow.com</span>
        </li>
        <li>
          <svg viewBox="0 0 24 24" aria-hidden="true"><g fill="none" stroke="#111" stroke-width="1.8"><circle cx="12" cy="12" r="9"/><ellipse cx="12" cy="12" rx="4" ry="9"/><path d="M3 12h18M5 7h14M5 17h14"/></g></svg>
          <span>thecopperlanternpinehollow.com</span>
        </li>
      </ul>
    </div>

    <div class="services">
      <span>Dine-in</span>
      <span>-</span>
      <span>Outdoor seating</span>
      <span>-</span>
      <span>In-store pickup</span>
    </div>
  </section>

</body>
</html>
```